Ridgeline Journeys business card

please see website
www.ridgelinejourneys.comau

info needed on card
Curtis Halvey
Ph
email
Adventure Riding GPS trails

please use my logo and colours off my site

Curtis Halvey
curtis@ridgelinejourneys.com

```html
<!DOCTYPE html>
<html lang="en">
<head>
<meta charset="utf-8">
<title>Ridgeline Journeys – Business Card</title>
<link href="https://fonts.googleapis.com/css2?family=Open+Sans:ital,wght@0,400;0,600;0,700;0,800;1,700&display=swap" rel="stylesheet">
<style>
  :root {
    --page-bg: #e9e7e4;
    --card-bg: #f7f7f6;
    --ink: #1c1c1c;
    --ink-soft: #555555;
    --rule: #9a9a9a;
    --accent: #f2d418;
  }
  * { box-sizing: border-box; margin: 0; padding: 0; }
  html, body {
    width: 1200px;
    height: 900px;
    overflow: hidden;
    background: var(--page-bg);
    font-family: "Open Sans", Arial, sans-serif;
  }
  .card {
    position: absolute;
    left: 275px;
    top: 250px;
    width: 650px;
    height: 400px;
    background: var(--card-bg);
    border-radius: 16px;
    box-shadow: 0 10px 30px rgba(0,0,0,0.12);
    overflow: hidden;
  }
  .brand {
    position: absolute;
    top: 72px;
    left: 0;
    right: 0;
    display: flex;
    justify-content: center;
    align-items: center;
    gap: 18px;
  }
  .brand-mark {
    width: 44px;
    height: 44px;
    border-radius: 50%;
    background: var(--accent);
  }
  .brand-name {
    font-weight: 800;
    font-size: 40px;
    color: var(--ink);
    letter-spacing: 0.5px;
  }
  .tagline {
    position: absolute;
    top: 182px;
    left: 0;
    right: 0;
    text-align: center;
    font-style: italic;
    font-weight: 700;
    font-size: 17px;
    color: var(--ink);
    letter-spacing: 0.3px;
  }
  .name-rule {
    position: absolute;
    top: 248px;
    left: 0;
    right: 0;
    display: flex;
    align-items: center;
    gap: 12px;
  }
  .name-rule::before,
  .name-rule::after {
    content: "";
    flex: 1;
    height: 1px;
    background: var(--rule);
  }
  .person-name {
    font-weight: 600;
    font-size: 21px;
    color: var(--ink-soft);
  }
  .contact-list {
    position: absolute;
    top: 288px;
    left: 0;
    right: 0;
    list-style: none;
    text-align: center;
    font-size: 17px;
    color: var(--ink);
    line-height: 27px;
  }
  .contact-list li {
    display: flex;
    justify-content: center;
    align-items: center;
    gap: 6px;
  }
  .contact-icon {
    width: 14px;
    height: 14px;
    fill: var(--ink-soft);
  }
</style>
</head>
<body>
  <div class="card">
    <div class="brand">
      <span class="brand-mark"></span>
      <span class="brand-name">Ridgeline Journeys</span>
    </div>
    <p class="tagline">ADVENTURE RIDING GPS TRAILS</p>
    <div class="name-rule"><span class="person-name">Curtis Halvey</span></div>
    <ul class="contact-list">
      <li>
        <svg class="contact-icon" viewBox="0 0 16 16" aria-hidden="true"><path d="M2 5c0-2 2-3 6-3s6 1 6 3v1h-3V5H5v1H2z M4 7h8l2 6H2z M8 8.5a2 2 0 1 0 0 4 2 2 0 0 0 0-4z"/></svg>
        (044)-555-0182
      </li>
      <li>
        <svg class="contact-icon" viewBox="0 0 16 16" aria-hidden="true"><path d="M1 3h14v10H1z M2 4v.5l6 4 6-4V4z" fill-rule="evenodd"/></svg>
        curtis@ridgelinejourneys.com
      </li>
      <li>
        <svg class="contact-icon" viewBox="0 0 16 16" aria-hidden="true"><path d="M6.5 9.5l3-3M5 8l-2 2a2.1 2.1 0 0 0 3 3l2-2M11 8l2-2a2.1 2.1 0 0 0-3-3L8 5" stroke="#555555" stroke-width="1.6" fill="none"/></svg>
        www.ridgelinejourneys.com
      </li>
    </ul>
  </div>
</body>
</html>
```